Cruise Booking Website

Cruise search and booking website

This project is a redesign of a cruise booking website we did a few years ago.

The current website is located here: http://voyage.pylonworks.example/en/

It's not fully functional but gives you ad idea how miserable the old design was.

All the information about cruises, cruise lines, destinations, ports and shore excursions will be similar to http://www.sailquest.example/
Actual search pages (form, results, single result, sailing and cabin selection, ship info, booking) will have EXACTLY the same info as sailquest.example

We like the style of http://harborfleetdesk.example, it's quite modern, good spacing, not overloaded with information. So you can use it as an example of what we like, not what we want as a final result for us. Please, don't copy it. The result should not be possible to resemble the harborfleetdesk.example, because our site has to be unique. This is important!
If you submit a design that clearly reminds another cruise site it will be rejected!

Also the mockup provided is just to give you the basic structure and show what information has to be present on the page. It doesn't mean the layout has to be the same as a mockup. The layout is up to the designer.

I've updated the mockup to be more generic so it doesn't confuse you:
https://files.boxvault.example/s/k7m2qp9wz4hx/Home%20page.png

When you're adding social sharing icons like plazanet/chirpline you have to use chinese ones instead:
https://files.boxvault.example/s/t3nr8vx5lc2e/chinese-social-icons.png
Originals: http://minilk.example/qR7t

We'll start with home page first and after it's approved inner pages can be designed.

I know the cost of the project doesn't look high, but the task is straight forward and doesn't require to be very original, it's better to follow existing design and layout patterns that proved to work well.
That's why I encourage you to choose a template to build the design on top of one of https://themeparlor.example/ themes if it will save the design work, will be easier and faster for you. So it will be more like a customization than a new design from scratch.

Mockups, site map and logo files:
- https://files.boxvault.example/sh/h48dm2rs73fkpw/QvnbW2Xz8e

Website tree:
- https://sheets.papernest.example/document/d/7xPqR2mLw9sTk4VbN8cHj3YzA6eUf5GdKo1iMnBv/edit?usp=sharing
Updates

So far a lot of designs are just copying http://www.harborfleetdesk.example/ - we don't like it!

We like the style of harborfleetdesk.example, it's quite modern, good spacing, not overloaded with information. So you can use it as an example of what we like, not what we want as a final result for us. Please, don't copy it. The result should not be possible to resemble the harborfleetdesk.example, because our site has to be unique. This is important!

Target Market(s)

Chinese travellers

Industry/Entity Type

Build

Requirements
Must have
• * White, blue and red
* Large spacing, not too much information cramped into a small space like sailquest.example or the current website
* More "hidden" info in popups, tabs and so on, so not to many things are visible at the same time
* Compatible with kestrel scaffold styling (for easier coding):
- http://kestrelkit.codeshelf.example/scaffold/index.html
- http://skinmarket.example/
* Feel free to propose to build the design on top of one of https://themeparlor.example/ themes if it will save the design work, will be easier and faster for you

```html
<!DOCTYPE html>
<html lang="en">
<head>
<meta charset="utf-8">
<title>HaiLang Cruises – Home</title>
<link href="https://fonts.googleapis.com/css2?family=Carlito:wght@400;700&display=swap" rel="stylesheet">
<style>
:root{
  --page:#3c80c2;
  --blue:#1a6fc0;
  --navy:#1d5d9c;
  --ink:#3b3b3b;
  --muted:#555;
  --red:#d41f1f;
  --line:#d6d6d6;
  --foot:#cfe2f0;
  --panel:rgba(25,40,60,.88);
}
*{box-sizing:border-box;margin:0;padding:0}
html,body{width:868px;height:1200px;overflow:hidden}
body{background:var(--page);font-family:"Carlito",sans-serif;color:var(--ink);font-size:10px}
.site{position:relative;width:868px;height:1200px}
.abs{position:absolute}
.column{left:86px;top:0;width:696px;height:1200px;background:#fff}
.topbar{right:100px;top:10px;display:flex;gap:10px;align-items:center;color:var(--blue);font-size:10px;font-weight:700}
.topbar .search{width:134px;height:18px;border:1px solid #ccc;background:#f4f4f4;position:relative}
.header{left:94px;top:32px;width:680px;height:78px;border:1px solid #dde8ef;border-radius:4px;background:linear-gradient(90deg,#fff,#e8f3f8 60%,#f5fafc)}
.brand{left:108px;top:42px;display:flex;align-items:center;gap:6px}
.brand .dot{width:38px;height:38px;border-radius:50%;background:var(--blue)}
.brand .name{font-size:34px;font-weight:700;color:var(--navy);line-height:1}
.brand .url{font-size:9px;font-weight:700;color:var(--navy);margin-top:2px}
.callus{right:102px;top:46px;text-align:right}
.callus .num{color:var(--red);font-size:17px;font-weight:700}
.callus .txt{color:var(--navy);font-size:11px;font-style:italic}
.nav{left:109px;top:98px;width:651px;height:28px;background:linear-gradient(#2a80cc,#1560ab);border-radius:3px;display:flex;align-items:center;justify-content:space-around;padding:0 8px}
.nav a{color:#fff;text-decoration:none;font-size:10px;font-weight:700}
.hero{left:94px;top:136px;width:680px;height:317px;background:linear-gradient(120deg,#8aa8bd,#c99a72 45%,#a06b4e 70%,#5a7590);border-radius:3px}
.dots{left:101px;top:420px;width:85px;height:21px;background:var(--blue);border-radius:2px;display:flex;gap:4px;align-items:center;padding-left:10px}
.dots i{width:12px;height:12px;border-radius:50%;background:#6ab6ec}
.dots i:first-child{background:#fff}
.finder{left:558px;top:148px;width:199px;height:290px;background:var(--panel);border-radius:3px;padding:6px 11px;color:#fff}
.finder h2{font-size:17px;font-weight:700;margin-bottom:5px}
.finder label{display:block;font-size:10px;font-weight:700;margin:6px 0 3px}
.sel{height:19px;background:#f2f2f2;color:#888;font-size:8.5px;border-radius:2px;padding:4px 5px;position:relative}
.sel::after{content:"▴▾";position:absolute;right:4px;top:2px;font-size:7px;line-height:7px;width:6px;color:#333}
.pair{display:flex;gap:6px}.pair>div{flex:1}
.finder .age{font-weight:400;font-size:9px}
.chk{display:flex;gap:8px;align-items:center;font-size:9.5px;margin-top:9px}
.chk i{width:10px;height:10px;background:#fff;border-radius:1px}
.btn-red{display:block;width:119px;height:18px;background:var(--red);color:#fff;font-size:8.5px;font-weight:700;text-align:center;line-height:18px;margin:10px 0 0 29px}
.tabs{left:94px;top:466px;display:flex;gap:5px}
.tabs span{height:27px;padding:0 11px;line-height:27px;background:#eef1f3;border:1px solid var(--line);border-bottom:0;color:var(--blue);font-weight:700;font-size:10px}
.tabs span.on{background:#fff;color:var(--red);height:28px}
.tabpane{left:94px;top:492px;width:449px;height:284px;border:1px solid var(--line);background:#fff}
.promo-photo{left:104px;top:511px;width:190px;height:145px;border:4px solid #fff;box-shadow:0 0 0 1px #ccc;background:linear-gradient(135deg,#c4302b,#e67060 50%,#9aa7b3)}
.promise{left:311px;top:508px;width:228px}
.promise h3{color:var(--red);font-size:13px;font-weight:700;margin-bottom:4px}
.promise p{font-size:10px;line-height:14.5px;color:var(--muted)}
.promise p b{color:var(--blue)}
.ticks{left:311px;top:582px;list-style:none}
.ticks li{display:flex;gap:10px;align-items:center;color:var(--blue);font-weight:700;font-size:10px;height:26px}
.pager{left:466px;top:753px;display:flex;gap:4px}
.pager i{width:9px;height:9px;border-radius:50%;background:#aaa}.pager i:first-child{background:var(--blue)}
.win{left:608px;top:466px;width:115px;height:104px;background:var(--blue);color:#fff;text-align:center;padding-top:7px;line-height:1}
.win .a{font-size:12px}.win .b{font-size:30px;font-weight:400;margin:3px 0 1px}.win .b sup{font-size:12px}
.win .c{font-size:25px;font-weight:700}.win .d{font-size:12px;margin-top:4px}
.news{left:556px;top:580px;width:218px;height:196px;border:1px solid var(--line);padding:6px 12px}
.news h3{color:var(--blue);font-size:13px;font-weight:700}
.news p{font-size:9px;line-height:14px;color:var(--muted);margin:2px 0 6px}
.field{height:20px;border:1px solid #ccc;font-size:8.5px;color:#999;padding:4px 7px;margin-bottom:5px;background:#fff}
.formfoot{display:flex;justify-content:space-between;align-items:center;margin-top:8px}
.formfoot a{color:var(--red);font-size:9px}
.btn-blue{background:var(--blue);color:#fff;font-size:9.5px;font-weight:700;padding:4px 11px;border:1px solid #0e4f8e}
.footer{left:86px;top:788px;width:696px;height:412px;background:var(--foot)}
.fcol h4{color:var(--red);font-size:12px;font-weight:700;margin-bottom:3px}
.fcol li{list-style:none;font-size:9px;line-height:16px;color:#444}
.fcol .more{color:var(--blue);font-weight:700;font-size:10.5px;display:block}
.community{left:398px;top:806px;width:202px;height:318px;background:#bcd6ea;padding:9px 14px}
.social{display:flex;gap:10px;align-items:center;font-size:9px;margin:8px 0 12px}
.social i{width:22px;height:22px;border-radius:2px;background:var(--blue)}
.community .field{background:#fff;height:19px;margin-bottom:6px}
.contact .logobox{width:86px;height:88px;border:1px solid #5c8fbe;background:#fff;display:flex;flex-direction:column;align-items:center;justify-content:center;gap:4px}
.logobox i{width:44px;height:44px;border-radius:50%;background:var(--blue)}
.logobox b{font-size:11px;color:var(--navy)}
.contact .row{display:flex;gap:8px;align-items:center;font-size:9px;line-height:17px}
.bottom{left:99px;top:1152px;width:675px;border-top:1px solid #7fb4dc;padding-top:9px;font-size:8.5px;color:#555;line-height:15px}
.bottom a{color:var(--red)}
.license{right:108px;top:1174px;font-size:8.5px;color:#555}
</style>
</head>
<body>
<div class="site">
  <div class="abs column"></div>

  <div class="abs topbar"><span>Sign In &nbsp;|&nbsp; Sign Up &nbsp;|&nbsp; 人民 ▾</span>
    <div class="search"><svg width="14" height="14" viewBox="0 0 14 14" style="position:absolute;right:3px;top:2px"><circle cx="5.5" cy="5.5" r="4" fill="none" stroke="#1a6fc0" stroke-width="2"/><path d="M8.5 8.5L13 13" stroke="#1a6fc0" stroke-width="2.4"/></svg></div>
  </div>

  <div class="abs header"></div>
  <div class="abs brand"><span class="dot"></span><div><div class="name">HaiLang</div><div class="url">www.hailangcruise.example</div></div></div>
  <div class="abs callus"><div class="num">1-800-555-0142</div><div class="txt">Call Us Today</div></div>

  <nav class="abs nav"><a>Home</a><a>Destinations</a><a>Curise Lines</a><a>Store Excrusion</a><a>Cruise Info</a><a>Deals</a><a>Online Booking</a><a>Contact Us</a></nav>

  <div class="abs hero" role="img" aria-label="Photo of a smiling couple embracing on a cruise ship deck"></div>
  <div class="abs dots"><i></i><i></i><i></i><i></i></div>

  <form class="abs finder">
    <h2>Find Your Cruise</h2>
    <label>Destination</label><div class="sel">Popular Dastinations</div>
    <div class="pair" style="margin-top:6px"><div><label>Length</label><div class="sel">Any Length</div></div><div><label>Month</label><div class="sel">Any Month</div></div></div>
    <label style="margin-top:10px">Cruise Line</label><div class="sel">Any Curise Line</div>
    <label style="margin-top:12px">Number of Travelers</label>
    <div class="pair"><div><label class="age">Age 25+</label><div class="sel">2</div></div><div><label class="age">Age 0 to 24</label><div class="sel">0</div></div></div>
    <div class="chk"><i></i>Check for senior rates</div>
    <span class="btn-red">SEARCH CRUISES</span>
  </form>

  <div class="abs tabs"><span class="on">Book With Us</span><span>Deals</span><span>Packages</span><span>News</span><span>First Time Cruiser</span></div>
  <div class="abs tabpane"></div>
  <div class="abs promo-photo" role="img" aria-label="Photo of a travel agent shaking hands with smiling customers in a cruise office"></div>
  <div class="abs promise"><h3>Our Promise</h3><p>At <b>HaiLang</b> , we are navigators of spectacular vacation experiences. As part of the number one brand in travel, this is our promise to you:</p></div>
  <ul class="abs ticks">
    <li><svg width="11" height="10" viewBox="0 0 11 10"><path d="M1 5l3 3 6-7" fill="none" stroke="#d41f1f" stroke-width="2.2"/></svg>Advice you can trust.</li>
    <li><svg width="11" height="10" viewBox="0 0 11 10"><path d="M1 5l3 3 6-7" fill="none" stroke="#d41f1f" stroke-width="2.2"/></svg>The best choice in prices.</li>
    <li><svg width="11" height="10" viewBox="0 0 11 10"><path d="M1 5l3 3 6-7" fill="none" stroke="#d41f1f" stroke-width="2.2"/></svg>Wayfarer Extras</li>
    <li><svg width="11" height="10" viewBox="0 0 11 10"><path d="M1 5l3 3 6-7" fill="none" stroke="#d41f1f" stroke-width="2.2"/></svg>More than cruises</li>
    <li><svg width="11" height="10" viewBox="0 0 11 10"><path d="M1 5l3 3 6-7" fill="none" stroke="#d41f1f" stroke-width="2.2"/></svg>Always there</li>
  </ul>
  <div class="abs pager"><i></i><i></i><i></i><i></i><i></i></div>

  <div class="abs win"><div class="a">ENTER TO <b>WIN A</b></div><div class="b"><sup>$</sup>5,000<sup>*</sup></div><div class="c">CRUISE</div><div class="d">VACATION FOR 2</div></div>

  <div class="abs news">
    <h3>Newsletter SignUp</h3>
    <p>Sign up for our newsletter and receive our best deals in your inbox.</p>
    <div class="field">First Name</div><div class="field">Email Address</div><div class="field">Phone Number</div><div class="field">Postal Zip</div>
    <div class="formfoot"><a>Contest Rules</a><span class="btn-blue">SUBSCRIBE</span></div>
  </div>

  <div class="abs footer"></div>

  <div class="abs fcol" style="left:99px;top:805px">
    <h4>Popular Cruise Lines</h4>
    <ul><li>Coralwind Cruise Lines</li><li>Stellaris Cruises</li><li>Marevista Cruises</li><li>Dreamharbor Cruise Line</li><li>Lowland Atlantic Line</li><li>Meridia Cruises</li><li>Nordbris Cruise Line</li><li>Duchess Cruises</li><li>Regal Antilles International</li></ul>
    <a class="more" style="margin-top:10px">See all cruise lines &gt;&gt;</a>
    <h4 style="margin-top:20px">Cruise by Type</h4>
    <ul><li>Popular Cruises</li><li>Luxury Cruises</li><li>River Cruises</li></ul>
    <a class="more" style="margin-top:24px">See All Cruise Types &gt;&gt;</a>
  </div>

  <div class="abs fcol" style="left:252px;top:805px">
    <h4>Land Vacations</h4>
    <ul><li>Hotels</li><li>Flights</li><li>Car Rentals</li><li>Vacation Packages</li><li>Shore Excursions</li></ul>
    <a class="more" style="margin-top:14px">See all land vacations &gt;&gt;</a>
    <h4 style="margin-top:20px">All About Cruising</h4>
    <ul><li>Frequently Asked Questions</li><li>First Time Cruisers</li><li>Value Comparison</li><li>Cruising with Kids</li><li>Vacation Packing Guide</li><li>Onboard Activities</li><li>Theme Cruises</li><li>Special Event Cruises</li></ul>
    <a class="more" style="margin-top:14px">See All About Cruising&gt;&gt;</a>
  </div>

  <div class="abs community fcol">
    <h4>Join Our Community</h4>
    <div class="social"><i></i>Like Us on Plazanet</div>
    <div class="social"><i></i>Follow Us on Chirpline</div>
    <h4 style="margin-top:14px">Free E-newsletter</h4>
    <p style="font-size:9px;line-height:13px;color:#444;margin-bottom:7px">Want great deals delivered to your inbox? Sign up for our free newsletter and you could win a free cruise for two!</p>
    <div class="field">First Name</div><div class="field">Email Address</div><div class="field">Phone Number</div><div class="field">Postal Zip</div>
    <div class="formfoot" style="margin-top:4px"><a style="color:var(--red);font-size:9px">Contest Rules</a><span class="btn-blue">SUBSCRIBE</span></div>
  </div>

  <div class="abs fcol contact" style="left:624px;top:815px;width:150px">
    <h4 style="margin-bottom:7px">Contact Us Today</h4>
    <div class="logobox"><i></i><b>HaiLang</b></div>
    <div style="color:var(--blue);font-weight:700;font-size:9px;margin-top:10px;line-height:17px">HAILANGCRUISE.EXAMPLE</div>
    <div class="row"><svg width="11" height="11" viewBox="0 0 11 11"><rect width="11" height="11" rx="2" fill="#d41f1f"/><path d="M3 2.5c-.5 2 1.5 5.5 5.5 6l.5-1.5-1.8-.8-.7.7c-1-.4-2-1.5-2.3-2.4l.7-.7-.7-1.8z" fill="#fff"/></svg>1-800-555-0142</div>
    <div class="row"><svg width="12" height="9" viewBox="0 0 12 9"><rect width="12" height="9" fill="#d41f1f"/><path d="M0 0l6 5 6-5" fill="none" stroke="#fff"/></svg>info@hailangcruise.example</div>
    <a class="more" style="font-size:9px">More...</a>
    <div style="display:flex;align-items:center;gap:5px;margin-top:12px"><span style="width:36px;height:36px;border-radius:50%;background:var(--blue)"></span><b style="font-size:10px;color:var(--navy)">HaiLang</b></div>
    <p style="font-size:9px;line-height:13px;color:#444;margin-top:10px">Established in 1987, HaiLang is a global leader in the marketing and sales of...</p>
    <a class="more" style="font-size:9px;margin-top:4px">More...</a>
  </div>

  <div class="abs bottom">Copyright 2013 <a>PylonWorks</a><br>Terms of Use / Privacy / Legal / Site Map / Reset Location / Feedback</div>
  <div class="abs license">TRL License Number: 4815-2</div>
</div>
</body>
</html>
```